Visitenkarte für Ergotherapiepraxis
Zielgruppe
Wir arbeiten mit Kindern und Erwachsene jeden Alters.
Diese Personen kommen mit Beeinträchtigungen (körperlich, seelisch, schulisch) im täglichen Leben zu uns. Wir unterstützen unsere Patienten die Beeinträchtigungen zu verringern oder zu kompensieren und so den Alltag besser bewältigen zu können.
Aufgabenstellung
Ein Design was Kinder und Erwachsene anspricht, aber nicht zu verspielt wirkt. Es soll vertrauenserweckend sein. Eventuell sollte die Visitenkarte ein "aufgehendes oder erblühendes oder aufsteigendes" Element enthalten (=zu Beginn war die Beeinträchtigung dann steigt die Lebensqualität als Folge der Behandlung)
Daten vorn:
Ergotherapiepraxis

```html
<!DOCTYPE html>
<html lang="de">
<head>
<meta charset="utf-8">
<title>Visitenkarte Ergotherapie Praxis</title>
<link rel="stylesheet" href="https://fonts.googleapis.com/css2?family=Fira+Sans:wght@400;500&display=swap">
<style>
  :root {
    --orange: #ff6600;
    --orange-soft: #ff8533;
    --ink: #1c1c1c;
    --text-dark: #2a2a2a;
    --white: #ffffff;
    --card-edge: #c9c9c9;
    --bg-center: #fbfbfb;
    --bg-edge: #dedede;
  }
  * { margin: 0; padding: 0; box-sizing: border-box; }
  html, body { width: 1200px; height: 1040px; overflow: hidden; }
  body {
    background: radial-gradient(ellipse at center, var(--bg-center) 0%, #f1f1f1 55%, var(--bg-edge) 100%);
    font-family: "Fira Sans", Arial, sans-serif;
    position: relative;
  }
  .card {
    position: absolute;
    top: 189px;
    width: 360px;
    height: 630px;
    overflow: hidden;
    text-align: center;
  }
  .card-front { left: 231px; background: var(--orange); color: var(--white); }
  .card-back {
    left: 610px;
    background: radial-gradient(ellipse at 50% 45%, #ffffff 0%, #f1f1f1 55%, #e2e2e2 100%);
    border: 1px solid var(--card-edge);
    color: var(--text-dark);
  }
  .role-title {
    position: absolute; top: 34px; left: 0; right: 0;
    font-size: 37px; font-weight: 400; line-height: 46px;
  }
  .mark-area {
    position: absolute;
    border-radius: 12px;
  }
  .card-front .mark-area {
    left: 36px; top: 199px; width: 288px; height: 276px;
    background: var(--orange-soft);
  }
  .card-back .mark-area {
    left: 93px; top: 220px; width: 174px; height: 170px;
    background: #f7dccb;
  }
  .name-band {
    position: absolute; left: 0; right: 0; bottom: 0; height: 60px;
    background: var(--ink); color: var(--white);
    font-size: 31px; line-height: 60px; letter-spacing: 0.5px;
  }
  .practice-title {
    position: absolute; top: 36px; left: 0; right: 0;
    font-size: 36px; font-weight: 500; line-height: 44px; color: #1e1e1e;
  }
  .practice-owner {
    position: absolute; top: 133px; left: 0; right: 0;
    font-size: 20px; letter-spacing: 0.5px; color: #222;
  }
  .address {
    position: absolute; top: 450px; left: 0; right: 0;
    font-size: 25px; line-height: 43px; color: var(--text-dark);
  }
  .phone-band {
    position: absolute; left: 0; right: 0; bottom: 0; height: 63px;
    background: var(--orange); color: var(--white);
    font-size: 37px; line-height: 63px;
  }
</style>
</head>
<body>
  <section class="card card-front">
    <h2 class="role-title">BEHANDELNDER<br>Therapeut</h2>
    <div class="mark-area" role="img" aria-label="Platz für das Praxis-Symbol: stehende Figur zwischen zwei Pfeilen"></div>
    <div class="name-band">WILMA ROTH</div>
  </section>

  <section class="card card-back">
    <h1 class="practice-title">ERGOTHERAPIE<br>Praxis</h1>
    <p class="practice-owner">WILMA ROTH</p>
    <div class="mark-area" role="img" aria-label="Platz für das Praxis-Symbol: stehende Figur zwischen zwei Pfeilen"></div>
    <address class="address" style="font-style:normal">Am Lindenweg | Hof 4<br>14812 Feldstadt, OT Birkau</address>
    <div class="phone-band">033845/47219</div>
  </section>
</body>
</html>
```